Tidal Forge - Crypto Currency Miner Powered by Renewable Energy Website

We Need Web Pages Design for Website for Crypto Currency Miner

Serivices include:
Mining Rig Sales
Housing for Rigs turnkey on renewable energy grid
Cloud Mining term packages
Updates

http://www.vaultrigsurvey.example (Competitors sites)

Target Market(s)

Investers for Mining Rigs and terms for 1,2 or 3 years of Hash rate

Industry/Entity Type

Mining

Number of Pages Required

5+ page

Font styles to use
Sans Serif

Colors
add136
9bcb3c
606060
474747
ffc214
cadf82
fbee3e
876aae
6b449b

Requirements
Must have
• Pictures of Solar, Wind and power Factor Correction units
Nice to have
• e-commerce platform so contract terms can be purchased through website
Should not have
• Heavy construction equipment

```html
<!DOCTYPE html>
<html lang="en">
<head>
<meta charset="utf-8">
<title>Tidal Forge – Home</title>
<link href="https://fonts.googleapis.com/css2?family=Roboto+Condensed:wght@300;400;700&family=Roboto:wght@300;400&display=swap" rel="stylesheet">
<style>
:root{
  --canvas:#ececec;
  --green-dark:#45ab52;
  --green-light:#68b86b;
  --green-foot:#279b41;
  --lime:#9bcb3c;
  --lime-bright:#add136;
  --amber:#ffc214;
  --lemon:#fbee3e;
  --row-tint:#ffe08a;
  --charcoal:#474747;
  --grey:#9c9c9c;
  --navy:#22237d;
  --white:#ffffff;
  --ink:#2b2b2b;
  --muted:#8a8a8a;
}
*{box-sizing:border-box;margin:0;padding:0}
html,body{width:1200px;height:1200px;overflow:hidden;background:var(--canvas)}
body{font-family:"Roboto Condensed",sans-serif;position:relative}
.page{position:absolute;left:336px;top:26px;width:529px;height:1148px;background:var(--white);box-shadow:0 6px 18px rgba(0,0,0,.18);overflow:hidden}
.section{position:absolute;left:0;width:529px}
.why{top:0;height:251px;background:var(--green-dark)}
.why::before{content:"";position:absolute;left:214px;top:0;width:315px;height:2px;background:#3a6b3f}
.about{top:251px;height:249px;background:var(--green-light)}
.prices{top:505px;height:373px;background:var(--amber)}
.footer{top:892px;height:164px;background:var(--charcoal)}
.base{top:1056px;height:92px;background:var(--green-foot)}
.abs{position:absolute}
.heading{font-size:16.5px;font-weight:400;color:var(--white);letter-spacing:-.2px}
.intro{width:153px;font-size:7.4px;line-height:9.6px;color:var(--white);font-weight:300;text-align:justify}
.body-copy{width:153px;font-size:4.6px;line-height:7px;color:var(--white);font-weight:300;text-align:justify}
.learn-more{width:55px;height:12px;border:1px solid var(--white);border-radius:2px;color:var(--white);font-size:5.4px;display:flex;align-items:center;justify-content:center}
.tile{width:82px;height:81px;border-radius:6px;display:flex;flex-direction:column;align-items:center;justify-content:flex-end;padding-bottom:11px;text-align:center;font-size:11px;line-height:11.5px;color:var(--white)}
.tile svg{margin-bottom:8px}
.tile.secure{background:var(--lime)}
.tile.mobile{background:var(--amber)}
.tile.wallet{background:var(--lemon);color:var(--ink)}
.tile.insured{background:var(--white);color:var(--ink);padding-bottom:6px}
.about-visual{left:261px;top:35px;width:187px;height:183px;border-radius:17px;background:radial-gradient(circle at 50% 40%,#dfeef5 0,#bcd7e3 22%,#f6f8f8 48%,#ffffff 70%)}
.prices-title{left:0;width:529px;top:25px;text-align:center;font-size:16.5px;color:var(--ink)}
.prices-sub{left:0;width:529px;top:49px;text-align:center;font-size:7px;color:var(--ink)}
.price-grid{left:99px;top:73px;width:333px;display:grid;grid-template-columns:repeat(4,82px);column-gap:1.6px}
.plan{height:63px;position:relative;text-align:center}
.plan .band{height:22px;display:flex;align-items:center;justify-content:center;font-size:11.5px;font-weight:300}
.plan .amount{font-size:16px;font-weight:300;margin-top:8px}
.plan .per{font-size:3.6px;margin-top:1px}
.plan .pointer{position:absolute;left:36px;bottom:-6px;width:0;height:0;border-left:5px solid transparent;border-right:5px solid transparent;border-top:6px solid}
.plan.tarif{background:var(--lemon);color:var(--ink)}
.plan.tarif .amount{font-size:8px;margin-top:8px}
.plan.tarif .per{padding:0 9px;line-height:4.4px}
.plan.start{background:var(--lime);color:var(--white)}
.plan.start .band{background:var(--lime-bright)}
.plan.start .pointer{border-top-color:var(--lime)}
.plan.pro{background:var(--grey);color:#3c3c3c}
.plan.pro .band{background:var(--charcoal)}
.plan.pro .pointer{border-top-color:var(--grey)}
.plan.premium{background:var(--navy);color:var(--white)}
.plan.premium .band{background:#2f3496}
.plan.premium .pointer{border-top-color:var(--navy)}
.feature-grid{left:99px;top:145px;width:333px;display:grid;grid-template-columns:repeat(4,82px);column-gap:1.6px}
.cell{height:22px;display:flex;align-items:center;justify-content:center;font-family:"Roboto",sans-serif;font-size:6.8px;font-weight:300;color:var(--muted);background:var(--white)}
.cell.label{justify-content:flex-start;padding-left:6px;font-family:"Roboto Condensed",sans-serif;font-size:5px;color:var(--ink);font-weight:400}
.cell.tint{background:var(--row-tint)}
.foot-title{font-size:11px;font-weight:300;color:var(--amber)}
.foot-title.lime{color:var(--lime)}
.foot-copy{font-size:5.8px;line-height:8.4px;color:#e8e8e8;font-weight:300}
.outline-btn{width:67px;height:13px;border:1px solid var(--amber);border-radius:2px;color:var(--amber);font-size:6px;display:flex;align-items:center;justify-content:center}
.outline-btn.lime{border-color:var(--lime);color:var(--lime)}
.social{width:14px;height:14px;border:1px solid var(--white);border-radius:50%}
.nav-link{font-size:5.8px;color:var(--white);font-weight:300}
.brand{display:flex;align-items:center;gap:4px;color:var(--white);font-size:10px;font-weight:700}
.brand .mark{width:14px;height:14px;border-radius:50%;background:var(--white)}
.card-name{font-size:5px;font-weight:700;color:var(--white)}
.base-copy{font-size:5.8px;line-height:8.2px;color:var(--white);font-weight:300}
</style>
</head>
<body>
<svg width="0" height="0" style="position:absolute">
  <defs>
    <symbol id="tick" viewBox="0 0 10 6"><polyline points="1,1 5,5 9,1" fill="none" stroke="#8a8a8a" stroke-width="1"/></symbol>
    <symbol id="cross" viewBox="0 0 8 8"><path d="M1 1L7 7M7 1L1 7" stroke="#555" stroke-width="1"/></symbol>
  </defs>
</svg>

<div class="page">

  <section class="section why">
    <h2 class="heading abs" style="left:77px;top:36px">Why Choose Tidal Forge?</h2>
    <p class="intro abs" style="left:77px;top:70px">Lorem ipsum dolor sit amet, consectetur adipisicing elit. Aliquam praesentium, distinctio dicta molestias dignissimos.</p>
    <p class="body-copy abs" style="left:77px;top:110px">Rigs run day and night on clean power from our own solar and wind parks. Each unit is tuned, cooled and watched by our team so your hash rate stays high.</p>
    <p class="body-copy abs" style="left:77px;top:146px">Choose a one, two or three year term and follow every payout from your phone. Our grid housing keeps costs low and our power factor units keep the load steady. Contracts are insured, wallets are kept offline and support is ready whenever you need help.</p>
    <div class="learn-more abs" style="left:175px;top:210px">Learn More</div>

    <div class="tile secure abs" style="left:258px;top:37px">
      <svg width="34" height="38" viewBox="0 0 34 38"><path d="M17 2L31 7V17C31 27 24 33 17 36C10 33 3 27 3 17V7Z" fill="none" stroke="#fff" stroke-width="1.6"/><circle cx="17" cy="16" r="4" fill="none" stroke="#fff" stroke-width="1.6"/><path d="M15 19L14 27H20L19 19" fill="none" stroke="#fff" stroke-width="1.6"/></svg>
      <span>Safe And Secure</span>
    </div>
    <div class="tile mobile abs" style="left:360px;top:37px">
      <svg width="38" height="38" viewBox="0 0 38 38"><rect x="4" y="3" width="18" height="32" rx="3" fill="none" stroke="#fff" stroke-width="1.6"/><circle cx="13" cy="16" r="5" fill="none" stroke="#fff" stroke-width="1.6"/><circle cx="28" cy="20" r="6" fill="none" stroke="#fff" stroke-width="1.6"/><circle cx="28" cy="20" r="2" fill="#fff"/><line x1="10" y1="31" x2="16" y2="31" stroke="#fff" stroke-width="1.6"/></svg>
      <span>Mobile App</span>
    </div>
    <div class="tile wallet abs" style="left:258px;top:132px">
      <svg width="40" height="36" viewBox="0 0 40 36"><rect x="4" y="6" width="32" height="22" rx="3" fill="none" stroke="#2b2b2b" stroke-width="1.6"/><rect x="28" y="13" width="9" height="8" rx="2" fill="none" stroke="#2b2b2b" stroke-width="1.6"/><path d="M6 22L10 20L14 22V28C14 31 10 33 10 33C10 33 6 31 6 28Z" fill="#fbee3e" stroke="#2b2b2b" stroke-width="1.4"/><polyline points="8,27 10,29 13,25" fill="none" stroke="#2b2b2b" stroke-width="1.2"/></svg>
      <span>Secure Wallet</span>
    </div>
    <div class="tile insured abs" style="left:360px;top:132px">
      <svg width="38" height="38" viewBox="0 0 38 38"><rect x="5" y="5" width="22" height="28" rx="2" fill="none" stroke="#2b2b2b" stroke-width="1.6"/><rect x="11" y="2" width="10" height="6" rx="1" fill="#fff" stroke="#2b2b2b" stroke-width="1.4"/><path d="M16 13L22 15V20C22 24 16 27 16 27C16 27 10 24 10 20V15Z" fill="none" stroke="#2b2b2b" stroke-width="1.4"/><circle cx="29" cy="29" r="5.5" fill="#fff" stroke="#2b2b2b" stroke-width="1.4"/><path d="M29 26V32M26 29H32" stroke="#2b2b2b" stroke-width="1.4"/></svg>
      <span>Covered By<br>Insurance</span>
    </div>
  </section>

  <section class="section about">
    <h2 class="heading abs" style="left:77px;top:37px">About Tidal Forge?</h2>
    <p class="intro abs" style="left:77px;top:71px">Lorem ipsum dolor sit amet, consectetur adipisicing elit. Aliquam praesentium, distinctio dicta molestias dignissimos.</p>
    <p class="body-copy abs" style="left:77px;top:111px">Rigs run day and night on clean power from our own solar and wind parks. Each unit is tuned, cooled and watched by our team so your hash rate stays high.</p>
    <p class="body-copy abs" style="left:77px;top:147px">Choose a one, two or three year term and follow every payout from your phone. Our grid housing keeps costs low and our power factor units keep the load steady. Contracts are insured, wallets are kept offline and support is ready whenever you need help.</p>
    <div class="learn-more abs" style="left:175px;top:203px">Learn More</div>
    <div class="about-visual abs" role="img" aria-label="Photo of a glass light bulb with a young green plant growing inside it from soil"></div>
  </section>

  <section class="section prices">
    <h2 class="prices-title abs">Prices</h2>
    <p class="prices-sub abs">Lorem ipsum dolor sit amet, consectetur adipisicing elit. Aliquam praesentium, distinctio dicta molestias</p>

    <div class="price-grid abs">
      <div class="plan tarif"><div class="band">TARIF</div><div class="amount">PRICING TABLE</div><div class="per">Compare our mining terms below</div></div>
      <div class="plan start"><div class="band">START</div><div class="amount">$29.99</div><div class="per">PER MONTH</div><span class="pointer"></span></div>
      <div class="plan pro"><div class="band"></div><div class="amount">$49.99</div><div class="per">PER MONTH</div><span class="pointer"></span></div>
      <div class="plan premium"><div class="band">PREMIUM</div><div class="amount">$69.99</div><div class="per">PER MONTH</div><span class="pointer"></span></div>
    </div>

    <div class="feature-grid abs">
      <div class="cell label">Consectetur adipiscing</div>
      <div class="cell"><svg width="7" height="7"><use href="#cross"/></svg></div>
      <div class="cell"><svg width="9" height="6"><use href="#tick"/></svg></div>
      <div class="cell"><svg width="9" height="6"><use href="#tick"/></svg></div>

      <div class="cell label tint">Adipiscing consectetur</div>
      <div class="cell tint">4 GB</div><div class="cell tint">16 GB</div><div class="cell tint">UNLIMITED</div>

      <div class="cell label">Pellentesque</div>
      <div class="cell">15 CONTACTS</div><div class="cell">30 CONTACTS</div><div class="cell">&gt;50 CONTACTS</div>

      <div class="cell label tint">Vitae purus</div>
      <div class="cell tint"><svg width="9" height="6"><use href="#tick"/></svg></div>
      <div class="cell tint"><svg width="9" height="6"><use href="#tick"/></svg></div>
      <div class="cell tint"><svg width="9" height="6"><use href="#tick"/></svg></div>

      <div class="cell label">Donec egestas nec</div>
      <div class="cell"><svg width="7" height="7"><use href="#cross"/></svg></div>
      <div class="cell"><svg width="7" height="7"><use href="#cross"/></svg></div>
      <div class="cell"><svg width="9" height="6"><use href="#tick"/></svg></div>

      <div class="cell label tint">Mauris interdum</div>
      <div class="cell tint"><svg width="9" height="6"><use href="#tick"/></svg></div>
      <div class="cell tint"><svg width="9" height="6"><use href="#tick"/></svg></div>
      <div class="cell tint"><svg width="9" height="6"><use href="#tick"/></svg></div>

      <div class="cell label">lacus in nisi molestie</div>
      <div class="cell">1 PERSON</div><div class="cell">4 PERSON</div><div class="cell">&gt;10 PERSON</div>

      <div class="cell label tint">lacus in nisi molestie</div>
      <div class="cell tint"><svg width="7" height="7"><use href="#cross"/></svg></div>
      <div class="cell tint"><svg width="9" height="6"><use href="#tick"/></svg></div>
      <div class="cell tint"><svg width="9" height="6"><use href="#tick"/></svg></div>

      <div class="cell label">Mauris ultrices</div>
      <div class="cell"><svg width="9" height="6"><use href="#tick"/></svg></div>
      <div class="cell"><svg width="9" height="6"><use href="#tick"/></svg></div>
      <div class="cell"><svg width="9" height="6"><use href="#tick"/></svg></div>

      <div class="cell label tint">Pellentesque</div>
      <div class="cell tint">4 GB</div><div class="cell tint">16 GB</div><div class="cell tint">UNLIMITED</div>
    </div>
  </section>

  <footer class="section footer">
    <h3 class="foot-title abs" style="left:85px;top:24px">Member Area</h3>
    <p class="foot-copy abs" style="left:85px;top:45px">If you don't have an account,<br>sign up for free.</p>
    <div class="outline-btn lime abs" style="left:86px;top:76px">SIGN UP</div>
    <div class="outline-btn abs" style="left:86px;top:102px">LOGIN</div>

    <h3 class="foot-title lime abs" style="left:190px;top:24px">Follow us</h3>
    <p class="foot-copy abs" style="left:190px;top:45px">Stay up to date with<br>Tidal Forge activities.</p>
    <span class="social abs" style="left:192px;top:83px"></span>
    <span class="social abs" style="left:214px;top:83px"></span>
    <span class="social abs" style="left:235px;top:83px"></span>
    <span class="social abs" style="left:192px;top:102px"></span>
    <span class="social abs" style="left:214px;top:102px"></span>
    <span class="social abs" style="left:235px;top:102px"></span>

    <a class="nav-link abs" style="left:286px;top:72px">HOME</a>
    <a class="nav-link abs" style="left:286px;top:86px">PRICING</a>
    <a class="nav-link abs" style="left:286px;top:101px">OUR OFFER</a>
    <a class="nav-link abs" style="left:344px;top:72px">ABOUT US</a>
    <a class="nav-link abs" style="left:344px;top:86px">DATACENTER</a>
    <a class="nav-link abs" style="left:344px;top:101px">PRESS</a>
    <a class="nav-link abs" style="left:405px;top:72px">PRIVACY</a>
    <a class="nav-link abs" style="left:405px;top:86px">CONTACT</a>
  </footer>

  <section class="section base">
    <div class="brand abs" style="left:88px;top:26px"><span class="mark"></span>Tidal Forge</div>
    <span class="card-name abs" style="left:186px;top:29px">Cardwell</span>
    <span class="card-name abs" style="left:212px;top:29px">Vexa</span>
    <span class="card-name abs" style="left:228px;top:29px">PayLoop</span>
    <p class="base-copy abs" style="left:182px;top:51px">We accept creditcard payment</p>
    <p class="base-copy abs" style="left:282px;top:29px">Address:<br>Tidal Forge.</p>
    <p class="base-copy abs" style="left:282px;top:54px">Address line here address<br>line here Address line here<br>address line here</p>
    <p class="base-copy abs" style="left:375px;top:29px">Address:<br>Tidal Forge.</p>
    <p class="base-copy abs" style="left:375px;top:54px">Address line here address<br>line here Address line here<br>address line here</p>
  </section>

</div>
</body>
</html>
```